BLS Business Card 2018

Larkmere Chiropractic. We have two locations that we want to advertise on the same card. Brightvale OrthoCore campus address: 3815 Pellham Dr., Suite 240, Flowood, MS 39417. Madison address: 246 Willowmere Dr., Building D., Madison, MS 39284. website: www.drlarkmere-example.com. o:(601)555-0147 f:(601)555-0183

Target Market(s)

Health care decision makers: primary care doctors and mothers

Contact Information for Business Card

I have no idea; up for any suggestions and I'd do much better picking from examples versus describing what I'm looking for. We are in a very high end location and would like the cards to look really sharp.

Requirements
Must have
• My name, Martin R Belvane, D.C.

```html
<!DOCTYPE html>
<html lang="en">
<head>
<meta charset="utf-8">
<title>Larkmere Chiropractic Business Card</title>
<link rel="stylesheet" href="https://fonts.googleapis.com/css2?family=Cinzel:wght@400;500&family=Open+Sans:wght@400;700&display=swap">
<style>
  :root {
    --stage: #0c0c0c;
    --card-dark: #3b3b3b;
    --card-light: #efefef;
    --ink-light: #f2f2f2;
    --ink-muted: #d6d6d6;
    --ink-dark: #3e3e3e;
    --rule: #8a8a8a;
  }
  * { margin: 0; padding: 0; box-sizing: border-box; }
  html, body { width: 1200px; height: 900px; overflow: hidden; background: var(--stage); }
  .canvas {
    width: 1200px; height: 900px;
    display: flex; flex-direction: column; align-items: center; justify-content: center; gap: 48px;
  }
  .card {
    width: 560px; height: 320px;
    display: flex; flex-direction: column; align-items: center; justify-content: center;
    text-align: center;
  }
  .card-front { background: var(--card-dark); color: var(--ink-light); }
  .card-back { background: var(--card-light); color: var(--ink-dark); }

  .brand { display: flex; align-items: center; gap: 16px; margin-bottom: 26px; }
  .brand-dot { width: 44px; height: 44px; border-radius: 50%; background: var(--ink-muted); }
  .brand-name {
    font-family: "Cinzel", serif; font-weight: 500; font-size: 30px;
    line-height: 1.05; text-align: left; letter-spacing: 1px; color: var(--ink-light);
    text-transform: uppercase;
  }
  .location-label {
    font-family: "Open Sans", sans-serif; font-weight: 700; font-size: 13px;
    letter-spacing: 0.5px; color: var(--ink-muted);
  }
  .location-address {
    font-family: "Open Sans", sans-serif; font-size: 14px; color: var(--ink-muted); margin-top: 2px;
  }

  .doctor-name {
    font-family: "Cinzel", serif; font-weight: 400; font-size: 21px; letter-spacing: 1px;
    text-transform: uppercase;
  }
  .contact-divider { display: flex; align-items: center; gap: 8px; margin: 8px 0 4px; }
  .contact-divider .rule { width: 62px; height: 1px; background: var(--rule); }
  .contact-icons { display: flex; gap: 5px; }
  .contact-list {
    font-family: "Open Sans", sans-serif; font-size: 14px; line-height: 1.4;
  }
  .short-rule { width: 60px; height: 1px; background: var(--rule); margin: 6px 0 6px; }
  .campus-label { font-family: "Open Sans", sans-serif; font-weight: 700; font-size: 13px; text-transform: uppercase; }
  .campus-address { font-family: "Open Sans", sans-serif; font-size: 14px; }
</style>
</head>
<body>
<main class="canvas">
  <section class="card card-front">
    <div class="brand">
      <span class="brand-dot"></span>
      <p class="brand-name">Larkmere<br>Chiropractic</p>
    </div>
    <p class="location-label">MADISON</p>
    <p class="location-address">246 Willowmere Dr., Building D., Madison, MS 39284.</p>
  </section>

  <section class="card card-back">
    <h1 class="doctor-name">Martin R Belvane, D.C.</h1>
    <div class="contact-divider">
      <span class="rule"></span>
      <span class="contact-icons">
        <svg width="11" height="11" viewBox="0 0 12 12" aria-label="phone"><path d="M2 1h3l1 3-2 1a7 7 0 0 0 3 3l1-2 3 1v3c-6 1-10-3-9-9z" fill="#3e3e3e"/></svg>
        <svg width="11" height="11" viewBox="0 0 12 12" aria-label="fax"><rect x="3" y="1" width="6" height="4" fill="#3e3e3e"/><rect x="1" y="5" width="10" height="5" rx="1" fill="#3e3e3e"/><rect x="3" y="8" width="6" height="3" fill="#efefef"/></svg>
        <svg width="11" height="11" viewBox="0 0 12 12" aria-label="web"><circle cx="6" cy="6" r="5" fill="#3e3e3e"/><path d="M1 6h10M6 1c-2 3-2 7 0 10M6 1c2 3 2 7 0 10" stroke="#efefef" stroke-width="0.8" fill="none"/></svg>
      </span>
      <span class="rule"></span>
    </div>
    <div class="contact-list">
      <p>(601)555-0147</p>
      <p>(601)555-0183</p>
      <p>www.drlarkmere-example.com</p>
    </div>
    <span class="short-rule"></span>
    <p class="campus-label">Brightvale OrthoCore Campus</p>
    <p class="campus-address">3815 Pellham Dr., Suite 240, Flowood, MS 39417.</p>
  </section>
</main>
</body>
</html>
```